business card for horse saddlery

after a new business card for our saddlery, i will add 2 logos we have previously used and they can be used (or not) . Any images can be used from our website also at www.harrowfields.net.au, I have also added our brand logo, which may be good to incorporate on back ? we have over 15, 000 items online, ship Australia Wide.

Target Market(s)

horse owners

Industry/Entity Type

Retail - Equestrian

Contact Information for Business Card

Harrowfield Horse Supplies, 1300 48 62 90, www.harrowfields.net.au, 27 Lindqvist Rd Marrowbank Q 4587

Requirements
Must have
• trailgem is our brand so trailgem logo on back as 'distributers of', easy to read
Nice to have
• professional but fun
Should not have
• double sided (description wont save double sided)

```html
<!DOCTYPE html>
<html lang="en">
<head>
<meta charset="utf-8">
<title>Harrowfield Horse Supplies – Business Card</title>
<link rel="stylesheet" href="https://fonts.googleapis.com/css2?family=Didact+Gothic&display=swap">
<style>
  :root {
    --backdrop: #2d2d2f;
    --card: #ffffff;
    --card-shade: #ececec;
    --ink: #1c1c1c;
    --ink-soft: #55575a;
    --brand-blue: #2b4f8e;
    --icon-blue: #3a9ad9;
  }
  * { box-sizing: border-box; margin: 0; padding: 0; }
  html, body {
    width: 1200px; height: 900px; overflow: hidden;
    background: var(--backdrop);
    font-family: "Didact Gothic", "Century Gothic", sans-serif;
  }
  .canvas { position: relative; width: 1200px; height: 900px; }
  .card {
    position: absolute; width: 620px; height: 354px;
    background: linear-gradient(135deg, var(--card) 55%, var(--card-shade) 100%);
    box-shadow: 0 12px 30px rgba(0,0,0,.45);
  }
  .card--back { left: 90px; top: 70px; }
  .card--front { left: 490px; top: 476px; }

  /* back: distributor lockup, mark above name */
  .distributor {
    position: absolute; left: 50%; top: 54%;
    transform: translate(-50%, -50%);
    display: flex; flex-direction: column; align-items: center;
  }
  .distributor__dot {
    width: 84px; height: 84px; border-radius: 50%;
    background: var(--brand-blue);
    margin-bottom: 14px;
  }
  .distributor__label {
    align-self: flex-start;
    font-size: 15px; color: var(--ink-soft);
    letter-spacing: .5px; margin-bottom: 2px;
  }
  .distributor__name {
    font-size: 52px; line-height: 1;
    color: var(--brand-blue); letter-spacing: 2px;
  }

  /* front: shop mark + contacts */
  .shop-mark {
    position: absolute; right: 66px; top: 34px;
    display: flex; flex-direction: column; align-items: flex-end; gap: 10px;
  }
  .shop-mark__dot {
    width: 84px; height: 84px; border-radius: 50%; background: var(--ink);
    margin-right: 40px;
  }
  .shop-mark__name { font-size: 22px; color: var(--ink); }

  .contact {
    position: absolute; left: 44px; bottom: 40px;
    list-style: none; font-size: 20px; color: var(--ink-soft);
  }
  .contact li { display: flex; align-items: center; gap: 10px; margin-top: 8px; }
  .contact svg { width: 20px; height: 20px; flex: none; }

  .address {
    position: absolute; right: 60px; bottom: 66px;
    font-style: normal; font-size: 20px; line-height: 1.5;
    color: var(--ink-soft);
  }
</style>
</head>
<body>
<main class="canvas">
  <section class="card card--back" aria-label="Card back">
    <div class="distributor">
      <span class="distributor__dot" aria-hidden="true"></span>
      <span class="distributor__label">Distributers Of</span>
      <span class="distributor__name">TRAILGEM</span>
    </div>
  </section>

  <section class="card card--front" aria-label="Card front">
    <div class="shop-mark">
      <span class="shop-mark__dot" aria-hidden="true"></span>
      <span class="shop-mark__name">harrowfields.net.au</span>
    </div>

    <ul class="contact">
      <li>
        <svg viewBox="0 0 20 20" aria-hidden="true"><path fill="var(--icon-blue)" d="M2 7c0-2 2-4 8-4s8 2 8 4v2h-4V7H6v2H2zM5 10h10l2 7H3z"/><circle cx="10" cy="13.5" r="2" fill="#fff"/></svg>
        1300 48 62 90
      </li>
      <li>
        <svg viewBox="0 0 20 20" aria-hidden="true"><circle cx="10" cy="10" r="8" fill="none" stroke="var(--icon-blue)" stroke-width="2"/><path d="M2 10h16M10 2c3 3 3 13 0 16M10 2c-3 3-3 13 0 16" fill="none" stroke="var(--icon-blue)" stroke-width="1.4"/></svg>
        www.harrowfields.net.au
      </li>
    </ul>

    <address class="address">
      27 Lindqvist Rd<br>
      Marrowbank Q 4587
    </address>
  </section>
</main>
</body>
</html>
```